Every Shelf Set Neatly or ESN Organized needs a business card design. ESN Organized is a professi

We need a business card design that is clean, sharp and conveys a sense of organization. I already have a logo.

Target Market(s)

Families (specifically mothers), small business owners, parents, seniors

Industry/Entity Type

Business

Contact Information for Business Card

My website is www.esnorganized-example.com and my Facebook page is http://www.sociallink-example.com/everyshelfsetneatly. The phone number is 418-552-7094 and I want to be listed as Lorna M. Pelham, Owner

Requirements
Must have
• My logo.

```html
<!DOCTYPE html>
<html lang="en">
<head>
<meta charset="UTF-8">
<title>ESN Organized — Business Card</title>
<link href="https://fonts.googleapis.com/css2?family=Open+Sans:wght@400;600;700&family=Montserrat:wght@400;500&display=swap" rel="stylesheet">
<style>
  :root {
    --page-bg: #e9e7e3;
    --card-white: #ffffff;
    --brand-blue: #2f8fe0;
    --brand-blue-light: #4aa6f0;
    --brand-blue-deep: #1f6fc4;
    --card-black: #111214;
    --card-black-soft: #26282c;
    --text-dark: #1c1c1e;
    --text-light: #ffffff;
  }
  * { box-sizing: border-box; margin: 0; padding: 0; }
  html, body {
    width: 1200px;
    height: 950px;
    overflow: hidden;
    background: var(--page-bg);
    font-family: "Open Sans", Arial, sans-serif;
  }
  .stage {
    position: relative;
    width: 1200px;
    height: 950px;
    display: flex;
    align-items: center;
    justify-content: center;
    gap: 110px;
  }
  .card {
    position: relative;
    width: 360px;
    height: 620px;
    border-radius: 6px;
    overflow: hidden;
    box-shadow: 0 14px 34px rgba(0,0,0,0.18);
  }

  /* Front card */
  .card-front { background: var(--card-white); }
  .front-logo {
    position: absolute;
    top: 78px;
    left: 0;
    right: 0;
    text-align: center;
    font-family: "Montserrat", Arial, sans-serif;
    font-weight: 500;
    color: var(--brand-blue);
  }
  .front-logo .logo-name {
    font-size: 30px;
    letter-spacing: 3px;
    text-transform: uppercase;
  }
  .front-logo .logo-tagline {
    margin-top: 8px;
    font-size: 14px;
    letter-spacing: 1.5px;
  }
  .front-panel {
    position: absolute;
    left: 0;
    right: 0;
    bottom: 0;
    height: 400px;
    background: linear-gradient(180deg, var(--brand-blue-light) 0%, var(--brand-blue) 55%, var(--brand-blue-deep) 100%);
  }
  .contact-block {
    position: absolute;
    left: 40px;
    right: 30px;
    bottom: 70px;
    color: var(--text-light);
  }
  .contact-name {
    font-size: 22px;
    font-weight: 700;
    letter-spacing: 0.5px;
    text-transform: uppercase;
    text-align: center;
  }
  .contact-role {
    font-size: 14px;
    font-weight: 400;
    letter-spacing: 1px;
    text-transform: uppercase;
    text-align: center;
    margin-top: 2px;
    margin-bottom: 26px;
  }
  .contact-line {
    font-size: 15px;
    line-height: 1.6;
  }
  .contact-line .label { font-weight: 700; }

  /* Back card */
  .card-back {
    background: radial-gradient(ellipse at 35% 30%, var(--card-black-soft) 0%, var(--card-black) 70%);
  }
  .back-logo {
    position: absolute;
    top: 235px;
    left: 0;
    right: 0;
    text-align: center;
    font-family: "Montserrat", Arial, sans-serif;
    font-weight: 400;
    font-size: 92px;
    letter-spacing: 4px;
    color: var(--brand-blue);
  }
  .back-web {
    position: absolute;
    bottom: 58px;
    left: 0;
    right: 0;
    text-align: center;
    color: var(--text-light);
    font-size: 14px;
    letter-spacing: 3px;
  }
</style>
</head>
<body>
  <main class="stage">
    <section class="card card-front" aria-label="Business card front">
      <div class="front-logo">
        <div class="logo-name">ESN Organized</div>
        <div class="logo-tagline">Every Shelf Set Neatly</div>
      </div>
      <div class="front-panel">
        <div class="contact-block">
          <p class="contact-name">Lorna M. Pelham</p>
          <p class="contact-role">Owner</p>
          <p class="contact-line"><span class="label">Phone:</span> 418-552-7094</p>
          <p class="contact-line"><span class="label">Web:</span> www.esnorganized-example.com</p>
          <p class="contact-line"><span class="label">Fb:</span> everyshelfsetneatly</p>
        </div>
      </div>
    </section>

    <section class="card card-back" aria-label="Business card back">
      <div class="back-logo">ESN</div>
      <p class="back-web">www.esnorganized-example.com</p>
    </section>
  </main>
</body>
</html>
```